Flaschenetiketten-Design in rechteckiger Grundform für Biermanufaktur
Zielgruppe
Wir repräsentieren eine Bier-Manufaktur in der Gründungsphase und sind auf der Suche nach einem Designvorschlag für die Flaschenetiketten.
Unsere Zielgruppe sind Liebhaber, die auf der Suche nach dem Speziellen und Lokalen sind. Der Biergenuss abseits des Massenmarktes soll im Entwurf sichtbar/transportiert werden. Die Bier-Manufaktur steht zeitgleich für Trend-Kreationen mit bodenständigem Ursprung.
Aufgabenstellung
Die Herkunft der Gründer Familie aus dem Schweizer Kanton Simplon soll im Vordergrund stehen, hierzu bitte das Familienwappen / einzelne Elemente siehe Dateiupload berücksichtigen.
Das Etikett soll eine rechteckige Grundform haben.
Folgende Angaben sollen sich im Etikett wiederfinden:
- Biersorte: 'Lager' (zukünftig soll es möglich sein, Biersorte auf dem Etikett zu wechseln)
Brand: 'Hearty Kandrom'
'Biermanufaktur Walliser Ursprungs'
Die Schrift soll klar und nicht zu verspielt sein.

```html
<!DOCTYPE html>
<html lang="de">
<head>
<meta charset="utf-8">
<title>Hearty Kandrom – Lagerbier Etikett</title>
<link rel="stylesheet" href="https://fonts.googleapis.com/css2?family=Josefin+Sans:wght@600;700&display=swap">
<style>
  :root {
    --page-bg: #f4f4f2;
    --label-cream: #dfcd89;
    --label-frame: #5a88cf;
    --ink: #2a2a2a;
    --emblem-fill: #5585cc;
  }
  * { margin: 0; padding: 0; box-sizing: border-box; }
  html, body {
    width: 844px;
    height: 1200px;
    overflow: hidden;
    background: var(--page-bg);
  }
  .canvas {
    position: relative;
    width: 844px;
    height: 1200px;
  }
  .label {
    position: absolute;
    left: 62px;
    top: 200px;
    width: 720px;
    height: 800px;
    background: var(--label-cream);
    border: 13px solid var(--label-frame);
    font-family: "Josefin Sans", sans-serif;
    color: var(--ink);
    text-align: center;
  }
  .emblem-area {
    position: absolute;
    left: 211px;
    top: 53px;
    width: 272px;
    height: 327px;
    background: var(--emblem-fill);
  }
  .beer-type {
    position: absolute;
    left: 0;
    right: 0;
    top: 386px;
    font-size: 31px;
    font-weight: 600;
    letter-spacing: 3px;
    line-height: 1;
  }
  .brand-name {
    position: absolute;
    left: 0;
    right: 0;
    top: 478px;
    font-size: 99px;
    font-weight: 700;
    line-height: 100px;
    letter-spacing: 3px;
  }
  .brand-name span { display: block; }
  .tagline {
    position: absolute;
    left: 0;
    right: 0;
    top: 691px;
    font-size: 21px;
    font-weight: 700;
    letter-spacing: 2.2px;
    line-height: 1;
  }
</style>
</head>
<body>
  <main class="canvas">
    <section class="label">
      <div class="emblem-area" role="img" aria-label="Platz für das Familienwappen der Gründerfamilie"></div>
      <p class="beer-type">- LAGERBIER -</p>
      <h1 class="brand-name"><span>HEARTY</span><span>KANDROM</span></h1>
      <p class="tagline">BIERMANUFAKTUR WALLISER URSPRUNGS</p>
    </section>
  </main>
</body>
</html>
```